Landscape design build company door flyer

I would like this flyer to convey a high-level of professionalism for a company that is excellent with communication with their clients as well as a company that does incredible installations

Went on vacation/holiday

```html
<!DOCTYPE html>
<html lang="en">
<head>
<meta charset="utf-8">
<title>Summit Ridge Builders – Outdoor Living Flyer</title>
<link href="https://fonts.googleapis.com/css2?family=Poppins:wght@400;500;600;700;800&display=swap" rel="stylesheet">
<style>
  :root {
    --navy: #0a2b40;
    --paper: #f1f1f1;
    --header-grey: #d3d3d3;
    --rule-grey: #9a9a9a;
    --ink: #141414;
    --stage: #8c8c8c;
    --white: #ffffff;
  }
  * { margin: 0; padding: 0; box-sizing: border-box; }
  html, body { width: 1200px; height: 933px; overflow: hidden; background: var(--stage); }
  .stage { position: relative; width: 1200px; height: 933px; overflow: hidden; }
  .flyer {
    position: absolute; left: 253px; top: 20px;
    width: 1097px; height: 1410px;
    transform: scale(0.633); transform-origin: 0 0;
    background: var(--paper);
    font-family: "Poppins", sans-serif; color: var(--ink);
    overflow: hidden;
  }
  .hero-art { position: absolute; inset: 0; width: 1097px; height: 663px; }
  .brand { position: absolute; left: 40px; top: 110px; width: 350px; text-align: center; color: var(--navy); }
  .brand-mark { display: inline-block; width: 26px; height: 26px; background: var(--navy); margin-bottom: 14px; }
  .brand-name { font-weight: 600; font-size: 27px; letter-spacing: 0.5px; line-height: 1; white-space: nowrap; }
  .brand-tag { font-weight: 600; font-size: 12px; letter-spacing: 0.5px; margin-top: 6px; }
  .headline {
    position: absolute; left: 50px; top: 280px;
    color: var(--white); font-weight: 800; font-size: 72px; line-height: 80px; letter-spacing: -2px;
    white-space: nowrap;
  }
  .section-title { font-weight: 800; font-size: 34px; line-height: 1; letter-spacing: -0.5px; }
  .section-title::after { content: ""; display: block; width: 95px; height: 5px; background: var(--rule-grey); margin-top: 12px; }
  .about { position: absolute; left: 50px; top: 690px; width: 465px; }
  .about p { margin-top: 16px; font-size: 17.4px; line-height: 21px; text-align: justify; hyphens: auto; }
  .services { position: absolute; left: 605px; top: 690px; }
  .services ul { list-style: none; margin-top: 18px; }
  .services li { display: flex; align-items: center; gap: 20px; font-size: 19px; font-weight: 500; height: 29.8px; white-space: nowrap; }
  .services svg { width: 19px; height: 19px; flex: none; }
  .works-rule { position: absolute; left: 0; right: 0; top: 1011px; height: 3px; background: var(--navy); }
  .works-label {
    position: absolute; left: 388px; top: 988px; width: 310px; height: 42px;
    background: var(--navy); color: var(--white);
    font-weight: 700; font-size: 26px; text-align: center; line-height: 42px;
  }
  .work { position: absolute; top: 1050px; width: 296px; height: 162px; }
  .work-deck { left: 57px; background: linear-gradient(180deg, #4f8a3a 0%, #6b7f52 40%, #8a4a2c 60%, #6d3520 100%); }
  .work-pool { left: 395px; background: radial-gradient(ellipse at 55% 55%, #46c2c6 0%, #3aa0a8 22%, #b9c3c4 40%, #8d9899 70%, #3f5a35 100%); }
  .work-patio { left: 733px; background: linear-gradient(180deg, #1d2c2a 0%, #3b4b52 35%, #6a5d58 60%, #8e5a3a 85%, #4a3a32 100%); }
  .footer-art { position: absolute; left: 0; top: 1258px; width: 1097px; height: 152px; }
  .phone {
    position: absolute; left: 68px; top: 1310px;
    display: flex; align-items: center; gap: 18px;
    color: var(--white); font-weight: 700; font-size: 62px; letter-spacing: -2px; line-height: 1;
    white-space: nowrap;
  }
  .phone svg { width: 40px; height: 44px; }
  .contact { position: absolute; left: 718px; top: 1296px; color: var(--navy); font-size: 21px; font-weight: 500; }
  .contact li { list-style: none; display: flex; align-items: center; gap: 28px; height: 36px; white-space: nowrap; }
  .contact svg { width: 24px; height: 24px; flex: none; }
</style>
</head>
<body>
<div class="stage">
  <article class="flyer">
    <svg class="hero-art" viewBox="0 0 1097 663">
      <defs>
        <linearGradient id="houseTone" x1="0" y1="0" x2="1" y2="1">
          <stop offset="0" stop-color="#4d6a3a"/>
          <stop offset="0.35" stop-color="#5b6466"/>
          <stop offset="0.7" stop-color="#4a5558"/>
          <stop offset="1" stop-color="#4a3226"/>
        </linearGradient>
      </defs>
      <rect x="0" y="0" width="1097" height="225" fill="var(--header-grey)"/>
      <polygon points="0,225 515,225 732,663 0,663" fill="var(--navy)"/>
      <polygon points="505,0 1097,0 1097,663 732,663 515,225 425,225" fill="url(#houseTone)" role="img" aria-label="Aerial photo of a two-storey house with a new paver driveway, steps and planted beds"/>
    </svg>

    <div class="brand">
      <span class="brand-mark"></span>
      <div class="brand-name">SUMMIT RIDGE BUILDERS</div>
      <div class="brand-tag">OUTDOOR LIVING SPACES</div>
    </div>

    <h1 class="headline">LET’S CREATE<br>YOUR DREAM<br>OUTDOOR<br>LIVING SPACE!</h1>

    <section class="about">
      <h2 class="section-title">ABOUT US</h2>
      <p>Discover the endless possibilities for your outdoor space with The Summit Ridge Builders Team. Our team of skilled artisans is dedicated to turning your outdoor space into a breathtaking oasis that you’ll love coming home to. Whether it’s a cozy patio for intimate gatherings, a sprawling deck to host memorable parties, or a custom paver driveway that adds instant curb appeal, our high-quality craftsmanship ensures stunning results that exceed your expectations.</p>
    </section>

    <section class="services">
      <h2 class="section-title">OUR SERVICES</h2>
      <ul>
        <li><svg viewBox="0 0 20 20"><circle cx="10" cy="10" r="10" fill="var(--navy)"/><path d="M5.5 10.3l3 3 6-6.3" fill="none" stroke="#fff" stroke-width="2.4"/></svg>Paver Patios</li>
        <li><svg viewBox="0 0 20 20"><circle cx="10" cy="10" r="10" fill="var(--navy)"/><path d="M5.5 10.3l3 3 6-6.3" fill="none" stroke="#fff" stroke-width="2.4"/></svg>Paver Driveways</li>
        <li><svg viewBox="0 0 20 20"><circle cx="10" cy="10" r="10" fill="var(--navy)"/><path d="M5.5 10.3l3 3 6-6.3" fill="none" stroke="#fff" stroke-width="2.4"/></svg>Retaining Walls</li>
        <li><svg viewBox="0 0 20 20"><circle cx="10" cy="10" r="10" fill="var(--navy)"/><path d="M5.5 10.3l3 3 6-6.3" fill="none" stroke="#fff" stroke-width="2.4"/></svg>Decks &amp; Railings</li>
        <li><svg viewBox="0 0 20 20"><circle cx="10" cy="10" r="10" fill="var(--navy)"/><path d="M5.5 10.3l3 3 6-6.3" fill="none" stroke="#fff" stroke-width="2.4"/></svg>Pools</li>
        <li><svg viewBox="0 0 20 20"><circle cx="10" cy="10" r="10" fill="var(--navy)"/><path d="M5.5 10.3l3 3 6-6.3" fill="none" stroke="#fff" stroke-width="2.4"/></svg>Outdoor Lighting</li>
        <li><svg viewBox="0 0 20 20"><circle cx="10" cy="10" r="10" fill="var(--navy)"/><path d="M5.5 10.3l3 3 6-6.3" fill="none" stroke="#fff" stroke-width="2.4"/></svg>Firepits &amp; Fireplaces</li>
      </ul>
    </section>

    <div class="works-rule"></div>
    <h2 class="works-label">OUR WORKS</h2>
    <div class="work work-deck" role="img" aria-label="Photo of a wooden deck with pergola and lounge chairs among trees"></div>
    <div class="work work-pool" role="img" aria-label="Aerial photo of a rectangular pool surrounded by a white deck"></div>
    <div class="work work-patio" role="img" aria-label="Photo of a paver patio at dusk with a round firepit, lit steps and a pool"></div>

    <svg class="footer-art" viewBox="0 0 1097 152" aria-hidden="true">
      <polygon points="668,0 1097,0 1097,152 610,152" fill="var(--header-grey)"/>
      <polygon points="0,22 662,22 610,152 0,152" fill="var(--navy)"/>
    </svg>

    <div class="phone">
      <svg viewBox="0 0 24 24"><path fill="#fff" d="M6.6 2.2c.6-.3 1.3-.1 1.6.5l2.1 4c.3.6.2 1.2-.3 1.6L8.3 9.6c1 2.4 3.2 4.8 5.8 6.1l1.4-1.6c.4-.5 1.100-.6 1.6-.3l3.9 2.3c.6.3.8 1 .5 1.6l-1 2.2c-.4.9-1.4 1.5-2.4 1.3C9.8 19.8 4 13.5 3.1 5.6c-.1-1 .4-1.9 1.3-2.4z"/></svg>
      <span>206-555-0148</span>
    </div>

    <ul class="contact">
      <li><svg viewBox="0 0 24 24"><rect x="1" y="5" width="22" height="15" rx="1.5" fill="var(--navy)"/><path d="M2 6.5l10 7 10-7" fill="none" stroke="#d3d3d3" stroke-width="1.8"/></svg>info@summitbuilders.com</li>
      <li><svg viewBox="0 0 24 24" fill="none" stroke="var(--navy)" stroke-width="1.6"><circle cx="12" cy="12" r="10"/><ellipse cx="12" cy="12" rx="4.5" ry="10"/><path d="M2 12h20M4 7h16M4 17h16"/></svg>www.summitbuilders.com</li>
    </ul>
  </article>
</div>
</body>
</html>
```